Build Website for Playful Brand that helps content creators build businesses

Please help me create a website for my company that helps content creators build businesses around their audience. I have attached a design and vibe that I am going for at mossquay.io.

Open for changes, but I want to keep the colour I currently have (a light teal). Ultimately the brand is playful but should come off as a very modern elevated brand.

I am looking for a few pages including

1. Home (with clear CTA button)
A section where I can input what the company does, and some brands that we have launched

2. About Me
A simple page, that has preferably able to put a circular image of myself and then give a quick background about the company

3. Blog (can you include how blog posts will appear and it should sit nicely in the page)
This ideally is a section that will be able to link to another software so my blogs automatically flow into here or posts. But otherwise it should have sections of blocks where creators can see about topics that I post about

4. Contact (this should include a form that will allow users to contact me)
Finally a contact page where it links my socials, similar what is there, but ideally there is a form they can fill out which I can link to my inbox as well. This should be a simple page as well

Create a multi page website, including a page that will link or can link blog post

Similar to this vibe and logo - https://mossquay.io/

Target Market(s)

Content Creators

Coding

Coded - Design and coding required

Number of Pages Required

4 page

Requirements
Must have
• Home, Contact Me (Including a place to submit an enquiry and form), Blog Post Page As well

```html
<!DOCTYPE html>
<html lang="en">
<head>
<meta charset="utf-8">
<title>Moss Quay — Building Businesses</title>
<link rel="stylesheet" href="https://fonts.googleapis.com/css2?family=Varela+Round&display=swap">
<style>
:root{
  --bg:#e6fdfd;
  --ink:#3f565c;
  --text:#333c3f;
  --muted:#9aa3a6;
  --sky:#cdebf3;
  --ice:#f4fbfd;
  --white:#ffffff;
  --gold:#d9a21b;
}
*{margin:0;padding:0;box-sizing:border-box}
html,body{width:1200px;height:4175px;overflow:hidden}
body{position:relative;background:var(--bg);font-family:"Varela Round",sans-serif;color:var(--text)}
.abs{position:absolute}
.backdrop{position:absolute;left:0;top:0}
a{color:inherit;text-decoration:none}

.brand{position:absolute;font-size:30px;line-height:32px;letter-spacing:3px;color:var(--ink);white-space:nowrap}
.brand-dot{position:absolute;border-radius:50%;background:var(--sky);border:5px solid var(--ink)}

.nav{position:absolute;top:63px;font-size:15px;color:var(--ink)}
.nav.active{border-bottom:2px solid var(--ink);padding-bottom:4px}
.login{position:absolute;left:945px;top:49px;width:109px;height:47px;border-radius:24px;background:var(--ink);color:var(--white);font-size:15px;display:flex;align-items:center;justify-content:center;gap:6px}

.btn{position:absolute;height:47px;border-radius:24px;background:var(--ink);color:var(--white);font-size:15px;display:flex;align-items:center;justify-content:center;box-shadow:0 3px 6px rgba(0,0,0,.15)}
.btn.light{background:var(--white);color:var(--ink)}

.hero-title{position:absolute;left:141px;top:322px;font-size:58px;color:var(--text);letter-spacing:1px;font-weight:400}
.hero-sub{position:absolute;left:143px;top:407px;font-size:18px;color:var(--text)}
.dots{position:absolute;display:flex;gap:12px}
.dots span{width:9px;height:9px;border-radius:50%;background:var(--white);opacity:.8}
.dots span.on{background:var(--ink);opacity:1}
.dots.grey span{background:#c7cfd1}
.dots.grey span.on{background:var(--ink)}

.section-title{position:absolute;font-size:45px;color:var(--text);font-weight:400;letter-spacing:1px}
.about-copy{position:absolute;left:637px;top:1030px;width:417px;font-size:14.5px;line-height:24.7px;text-align:justify;color:var(--text)}

.testimonial{position:absolute;width:441px;height:218px;border-radius:50%;background:var(--ice);box-shadow:6px 10px 10px rgba(60,80,85,.25)}
.avatar{position:absolute;left:42px;top:56px;width:104px;height:104px;border-radius:50%;background:linear-gradient(160deg,#c9b59f,#8a6f58);border:3px solid var(--white)}
.avatar.alt{background:linear-gradient(160deg,#e9e4df,#9a8070)}
.quote{position:absolute;left:144px;top:58px;width:245px;font-size:14px;line-height:22.5px;font-style:italic;text-align:justify;color:var(--text)}
.reviewer{position:absolute;left:144px;top:158px;font-size:14px;color:var(--text);display:flex;align-items:center;gap:12px}
.stars{display:flex;gap:1px}

.post{position:absolute;width:295px;background:var(--white);box-shadow:0 2px 4px rgba(0,0,0,.12)}
.post-img{width:295px;height:217px}
.post-body{padding:0 15px}
.post-title{font-size:16.5px;line-height:28px;color:var(--text)}
.post-excerpt{font-size:11.5px;line-height:24px;color:var(--muted);margin-top:8px}
.post-meta{font-size:10.5px;color:var(--muted);margin-top:16px;display:flex;align-items:center;gap:6px}

.partner{position:absolute;top:2986px;width:221px;height:120px;border-radius:50%;background:var(--white);display:flex;align-items:center;justify-content:center;gap:10px;font-size:26px;color:var(--ink)}
.partner.lifted{box-shadow:4px 10px 10px rgba(60,80,85,.25)}
.partner i{width:24px;height:24px;border-radius:50%;background:var(--ink)}

.contact-title{position:absolute;left:0;width:1200px;text-align:center;top:3356px;font-size:45px;color:var(--white);font-weight:400;letter-spacing:1px}
.mail-icon{position:absolute;left:446px;top:3426px;width:68px;height:68px;border-radius:50%;background:var(--white);display:flex;align-items:center;justify-content:center}
.mail-text{position:absolute;left:535px;top:3444px;font-size:26px;color:var(--white)}
.field{position:absolute;border-bottom:1.5px solid #b9c6c9;color:var(--white);font-size:12px}

.social{position:absolute;top:3999px;width:32px;height:32px;border-radius:50%;background:var(--ink)}
.foot-nav{position:absolute;top:4059px;font-size:17px;color:var(--ink)}
.copyright{position:absolute;left:556px;top:4105px;font-size:12px;color:var(--ink)}
</style>
</head>
<body>

<svg class="backdrop" width="1200" height="4175" viewBox="0 0 1200 4175" aria-hidden="true">
  <defs>
    <linearGradient id="heroScene" x1="0" y1="0" x2="0" y2="1">
      <stop offset="0" stop-color="#f2f5f7"/>
      <stop offset=".45" stop-color="#dfe7ec"/>
      <stop offset=".7" stop-color="#aebfcc"/>
      <stop offset="1" stop-color="#cdd9e2"/>
    </linearGradient>
  </defs>
  <path d="M180 200 C450 135 900 148 1100 265 C1205 335 1195 570 1120 705 C1030 865 740 892 520 862 C300 832 28 702 24 482 C22 335 80 242 180 200 Z" fill="var(--bg)" stroke="#3f565c" stroke-width="8"/>
  <g role="img" aria-label="Photograph of a polar bear standing on an ice floe over calm arctic water">
    <path transform="translate(600 515) scale(.95 .93) translate(-600 -515)" d="M180 200 C450 135 900 148 1100 265 C1205 335 1195 570 1120 705 C1030 865 740 892 520 862 C300 832 28 702 24 482 C22 335 80 242 180 200 Z" fill="url(#heroScene)"/>
  </g>
  <path d="M150 1455 C350 1378 800 1368 1020 1448 C1182 1508 1200 1700 1140 1842 C1060 2022 800 2117 640 2114 C430 2110 200 2030 70 1880 C0 1790 10 1540 150 1455 Z" fill="var(--bg)" stroke="#3f565c" stroke-width="8"/>
  <path transform="translate(600 1750) scale(.955 .94) translate(-600 -1750)" d="M150 1455 C350 1378 800 1368 1020 1448 C1182 1508 1200 1700 1140 1842 C1060 2022 800 2117 640 2114 C430 2110 200 2030 70 1880 C0 1790 10 1540 150 1455 Z" fill="#cdebf3"/>
  <path d="M160 3300 C380 3222 800 3215 1030 3275 C1190 3320 1205 3560 1150 3700 C1060 3890 820 3960 640 3955 C420 3950 190 3880 70 3730 C0 3640 10 3390 160 3300 Z" fill="var(--bg)" stroke="#3f565c" stroke-width="8"/>
  <path transform="translate(600 3590) scale(.955 .935) translate(-600 -3590)" d="M160 3300 C380 3222 800 3215 1030 3275 C1190 3320 1205 3560 1150 3700 C1060 3890 820 3960 640 3955 C420 3950 190 3880 70 3730 C0 3640 10 3390 160 3300 Z" fill="#3f565c"/>
</svg>

<header>
  <span class="brand-dot" style="left:230px;top:14px;width:62px;height:62px"></span>
  <a class="brand" href="https://mossquay.io/" style="left:143px;top:110px">MOSS QUAY</a>
  <nav>
    <a class="nav active" href="#" style="left:513px">HOME</a>
    <a class="nav" href="#" style="left:610px">ABOUT ME</a>
    <a class="nav" href="#" style="left:741px">BLOG</a>
    <a class="nav" href="#" style="left:832px">CONTACT</a>
    <a class="login" href="#">
      <svg width="15" height="15" viewBox="0 0 16 16" fill="none" stroke="#fff" stroke-width="1.5"><circle cx="8" cy="5" r="3.2"/><path d="M2 15c0-3.5 2.7-5.5 6-5.5s6 2 6 5.5"/></svg>LOGIN</a>
  </nav>
</header>

<section class="hero">
  <h1 class="hero-title">BUILDING BUSINESSES</h1>
  <p class="hero-sub">Helping Content Creators Build Their Own Brand</p>
  <a class="btn" href="#" style="left:144px;top:461px;width:150px">GET STARTED</a>
  <div class="dots" style="left:576px;top:768px"><span></span><span class="on"></span><span></span></div>
</section>

<section class="about">
  <div class="abs" role="img" aria-label="Illustration of a friendly polar bear mascot standing on a patch of ice" style="left:141px;top:957px;width:446px;height:284px;border-radius:50% 50% 45% 45%;background:radial-gradient(ellipse at 50% 40%,#e9f6fb 0%,#c7e4ef 60%,#b3d6e3 100%)"></div>
  <h2 class="section-title" style="left:637px;top:960px">ABOUT US</h2>
  <p class="about-copy">Founded in 2024, we provide the highest level of goods and service.Sed ut perspiciatis unde omnis iste natus error sit voluptatem accusantium doloremque laudantium, totam rem aperiam, eaque ipsa quae ab illo inventore veritatis et quasi architecto beatae vitae dicta sunt explicabo. Nemo enim ipsam voluptq sit aspernatur aut odit aut fugitdantium, totam rem aperiam, eaque ipsa quae ab illo inventore veritatis et quasi architecto beatae vitae dicta sunt exp</p>
  <a class="btn" href="#" style="left:637px;top:1255px;width:150px">READ MORE</a>
</section>

<section class="testimonials">
  <h2 class="section-title" style="left:0;width:1200px;text-align:center;top:1543px">TESTIMONIALS</h2>
  <article class="testimonial" style="left:146px;top:1650px">
    <div class="avatar" role="img" aria-label="Portrait photo of the client"></div>
    <p class="quote">“Vvitae dicta sunt explicabo. Nemo enim ipsam voluptq sit aspernatur aut odit aut fugitdantium, totam rem aperiam, eaque ipsa”</p>
    <div class="reviewer">ROWAN HALE
      <span class="stars">
        <svg width="85" height="16" viewBox="0 0 85 16"><g fill="none" stroke="#d9a21b" stroke-width="1.3"><polygon points="8,1 10,6 15,6 11,9.5 12.5,15 8,11.7 3.5,15 5,9.5 1,6 6,6"/><polygon transform="translate(17 0)" points="8,1 10,6 15,6 11,9.5 12.5,15 8,11.7 3.5,15 5,9.5 1,6 6,6"/><polygon transform="translate(34 0)" points="8,1 10,6 15,6 11,9.5 12.5,15 8,11.7 3.5,15 5,9.5 1,6 6,6"/><polygon transform="translate(51 0)" points="8,1 10,6 15,6 11,9.5 12.5,15 8,11.7 3.5,15 5,9.5 1,6 6,6"/><polygon transform="translate(68 0)" points="8,1 10,6 15,6 11,9.5 12.5,15 8,11.7 3.5,15 5,9.5 1,6 6,6"/></g></svg>
      </span>
    </div>
  </article>
  <article class="testimonial" style="left:613px;top:1650px;box-shadow:none">
    <div class="avatar alt" role="img" aria-label="Portrait photo of the client"></div>
    <p class="quote">“Vvitae dicta sunt explicabo. Nemo enim ipsam voluptq sit aspernatur aut odit aut fugitdantium, totam rem aperiam, eaque ipsa”</p>
    <div class="reviewer">ROWAN HALE
      <span class="stars">
        <svg width="85" height="16" viewBox="0 0 85 16"><g fill="none" stroke="#d9a21b" stroke-width="1.3"><polygon points="8,1 10,6 15,6 11,9.5 12.5,15 8,11.7 3.5,15 5,9.5 1,6 6,6"/><polygon transform="translate(17 0)" points="8,1 10,6 15,6 11,9.5 12.5,15 8,11.7 3.5,15 5,9.5 1,6 6,6"/><polygon transform="translate(34 0)" points="8,1 10,6 15,6 11,9.5 12.5,15 8,11.7 3.5,15 5,9.5 1,6 6,6"/><polygon transform="translate(51 0)" points="8,1 10,6 15,6 11,9.5 12.5,15 8,11.7 3.5,15 5,9.5 1,6 6,6"/><polygon transform="translate(68 0)" points="8,1 10,6 15,6 11,9.5 12.5,15 8,11.7 3.5,15 5,9.5 1,6 6,6"/></g></svg>
      </span>
    </div>
  </article>
  <a class="btn" href="#" style="left:525px;top:1901px;width:150px">LOAD MORE</a>
</section>

<section class="blog">
  <h2 class="section-title" style="left:0;width:1200px;text-align:center;top:2190px">BLOG POSTS</h2>

  <article class="post" style="left:148px;top:2276px;height:418px">
    <div class="post-img" role="img" aria-label="Photo of a smiling creator filming herself at home" style="background:linear-gradient(140deg,#c9a27e,#7f8f92 60%,#4e6a74)"></div>
    <div class="post-body" style="padding-top:20px">
      <h3 class="post-title" style="font-weight:400">Sed ut perspiciatis unde omnis iste natus error sit ..</h3>
      <p class="post-excerpt">Lorem ipsum dolor sit amet, consectetur adipiscing elitsed do eiusmod tempor..</p>
      <p class="post-meta">
        <svg width="11" height="11" viewBox="0 0 16 16" fill="none" stroke="#9aa3a6" stroke-width="1.5"><circle cx="8" cy="5" r="3.2"/><path d="M2 15c0-3.5 2.7-5.5 6-5.5s6 2 6 5.5"/></svg>By Admin
        <svg style="margin-left:12px" width="11" height="11" viewBox="0 0 16 16" fill="none" stroke="#9aa3a6" stroke-width="1.5"><rect x="1.5" y="3" width="13" height="11.5"/><path d="M1.5 7h13M5 1v3M11 1v3"/></svg>November 10 , 2017
      </p>
    </div>
  </article>

  <article class="post" style="left:453px;top:2276px;height:418px">
    <div class="post-body" style="padding-top:20px;height:201px">
      <h3 class="post-title" style="font-weight:400">Sed ut perspiciatis unde omnis iste natus error sit ..</h3>
      <p class="post-excerpt">Lorem ipsum dolor sit amet, consectetur adipiscing elitsed do eiusmod tempor..</p>
      <p class="post-meta">
        <svg width="11" height="11" viewBox="0 0 16 16" fill="none" stroke="#9aa3a6" stroke-width="1.5"><circle cx="8" cy="5" r="3.2"/><path d="M2 15c0-3.5 2.7-5.5 6-5.5s6 2 6 5.5"/></svg>By Admin
        <svg style="margin-left:12px" width="11" height="11" viewBox="0 0 16 16" fill="none" stroke="#9aa3a6" stroke-width="1.5"><rect x="1.5" y="3" width="13" height="11.5"/><path d="M1.5 7h13M5 1v3M11 1v3"/></svg>November 10 , 2017
      </p>
    </div>
    <div class="post-img" role="img" aria-label="Photo of a camera on a tripod recording a creator" style="background:linear-gradient(140deg,#9fc0cf,#5b6d75 55%,#2f3a3f)"></div>
  </article>

  <article class="post" style="left:757px;top:2276px;height:418px">
    <div class="post-img" role="img" aria-label="Photo of a creator presenting a skincare product on camera" style="background:linear-gradient(140deg,#6e6a66,#c8864e 55%,#d9d3cc)"></div>
    <div class="post-body" style="padding-top:20px">
      <h3 class="post-title" style="font-weight:400">Sed ut perspiciatis unde omnis iste natus error sit ..</h3>
      <p class="post-excerpt">Lorem ipsum dolor sit amet, consectetur adipiscing elitsed do eiusmod tempor..</p>
      <p class="post-meta">
        <svg width="11" height="11" viewBox="0 0 16 16" fill="none" stroke="#9aa3a6" stroke-width="1.5"><circle cx="8" cy="5" r="3.2"/><path d="M2 15c0-3.5 2.7-5.5 6-5.5s6 2 6 5.5"/></svg>By Admin
        <svg style="margin-left:12px" width="11" height="11" viewBox="0 0 16 16" fill="none" stroke="#9aa3a6" stroke-width="1.5"><rect x="1.5" y="3" width="13" height="11.5"/><path d="M1.5 7h13M5 1v3M11 1v3"/></svg>November 10 , 2017
      </p>
    </div>
  </article>

  <a class="btn" href="#" style="left:525px;top:2735px;width:150px">LOAD MORE</a>
</section>

<section class="partners">
  <h2 class="section-title" style="left:0;width:1200px;text-align:center;top:2886px">OUR PARTNERS</h2>
  <div class="partner" style="left:144px"><i></i>Plinth</div>
  <div class="partner lifted" style="left:375px"><i></i>Ipsora</div>
  <div class="partner" style="left:605px"><i></i>Lumo</div>
  <div class="partner" style="left:835px"><i></i>Arvela</div>
  <div class="dots grey" style="left:576px;top:3170px"><span></span><span class="on"></span><span></span></div>
</section>

<section class="contact">
  <div class="abs" role="img" aria-label="Illustration of the polar bear mascot peeking over the contact panel" style="left:800px;top:3203px;width:270px;height:150px;border-radius:50% 50% 45% 45%;background:radial-gradient(ellipse at 55% 40%,#e9f6fb 0%,#c7e4ef 60%,#b3d6e3 100%)"></div>
  <h2 class="contact-title">CONTACT ME</h2>
  <div class="mail-icon">
    <svg width="26" height="20" viewBox="0 0 26 20"><rect x="1" y="1" width="24" height="18" rx="2" fill="#3f565c"/><path d="M2 3l11 8 11-8" fill="none" stroke="#fff" stroke-width="2"/></svg>
  </div>
  <a class="mail-text" href="#">hello@mossquay.io</a>
  <form>
    <label class="field" style="left:165px;top:3551px;width:268px;height:36px">Enter Name</label>
    <label class="field" style="left:465px;top:3551px;width:270px;height:36px">Enter Email</label>
    <label class="field" style="left:767px;top:3551px;width:268px;height:36px">Phone</label>
    <label class="field" style="left:165px;top:3615px;width:870px;height:69px">Message</label>
    <button class="btn light" type="submit" style="left:524px;top:3732px;width:151px;border:none;font-family:inherit">SUBMIT</button>
  </form>
</section>

<footer>
  <span class="brand-dot" style="left:282px;top:3975px;width:80px;height:80px"></span>
  <a class="brand" href="https://mossquay.io/" style="left:188px;top:4095px;font-size:35px;line-height:38px">MOSS QUAY</a>
  <a class="social" href="#" aria-label="Social profile" style="left:557px"></a>
  <a class="social" href="#" aria-label="Social profile" style="left:608px"></a>
  <a class="foot-nav" href="#" style="left:556px">HOME</a>
  <a class="foot-nav" href="#" style="left:670px">ABOUT ME</a>
  <a class="foot-nav" href="#" style="left:821px">BLOG</a>
  <a class="foot-nav" href="#" style="left:928px">CONTACT</a>
  <p class="copyright">© 2024. Moss Quay All Rights Reserved &nbsp;|&nbsp; Privacy &nbsp;|&nbsp; Terms of Use</p>
</footer>

</body>
</html>
```